Business Card Design

We provide services doing multiple jobs in the construction industry.Please note: The company name needs to be ROCK SOLID BUILDING SERVICESAttached logo was an example of what we wanted. Can you change up the colors?

Industry/Entity Type

Construction

Contact Information for Business Card

ROCK SOLID BUILDING SERVICES5401 HUDSON BEND RDAUSTIN, TX 78734(512)243-6854ROCKSOLIDBUILDINGSERVICES@GMAIL.COM

```html
<!DOCTYPE html>
<html lang="en">
<head>
<meta charset="utf-8">
<title>Pearlwood Framing Works – Business Card</title>
<link rel="stylesheet" href="https://fonts.googleapis.com/css2?family=Cinzel:wght@400;700&family=Arimo:wght@400&display=swap">
<style>
  :root {
    --backdrop: #e9e7e3;
    --card: #ffffff;
    --ink: #1c1c1c;
    --accent: #3b2f7a;
    --icon-glyph: #ffffff;
  }
  html, body {
    margin: 0;
    padding: 0;
    width: 1200px;
    height: 800px;
    overflow: hidden;
    background: var(--backdrop);
  }
  .stage {
    position: relative;
    width: 1200px;
    height: 800px;
  }
  .business-card {
    position: absolute;
    left: 100px;
    top: 115px;
    width: 1000px;
    height: 571px;
    background: var(--card);
    box-shadow: 0 6px 24px rgba(0,0,0,0.18);
  }
  .brand-mark {
    position: absolute;
    left: 70px;
    top: 60px;
    display: flex;
    align-items: center;
    gap: 14px;
  }
  .brand-mark__square {
    width: 40px;
    height: 40px;
    background: var(--accent);
  }
  .brand-mark__name {
    font-family: "Cinzel", serif;
    font-weight: 700;
    font-size: 26px;
    line-height: 1.1;
    color: var(--accent);
    letter-spacing: 1px;
  }
  .company-name {
    position: absolute;
    right: 70px;
    top: 175px;
    margin: 0;
    text-align: right;
    font-family: "Cinzel", serif;
    font-weight: 400;
    font-size: 36px;
    line-height: 1.15;
    letter-spacing: 2px;
    color: var(--ink);
  }
  .contact-list {
    position: absolute;
    left: 70px;
    top: 300px;
    margin: 0;
    padding: 0;
    list-style: none;
  }
  .contact-item {
    display: flex;
    align-items: center;
    gap: 18px;
    height: 42px;
    font-family: "Arimo", sans-serif;
    font-size: 23px;
    color: var(--ink);
  }
  .contact-item__icon {
    width: 30px;
    height: 30px;
    flex: none;
  }
  .contact-item__icon rect { fill: var(--accent); }
  .contact-item__icon .glyph { fill: var(--icon-glyph); }
  .contact-item__icon .glyph-line { fill: none; stroke: var(--icon-glyph); stroke-width: 1.6; }
</style>
</head>
<body>
<main class="stage">
  <article class="business-card">
    <div class="brand-mark">
      <span class="brand-mark__square"></span>
      <span class="brand-mark__name">PEARLWOOD<br>FRAMING WORKS</span>
    </div>

    <h1 class="company-name">PEARLWOOD FRAMING<br>WORKS</h1>

    <ul class="contact-list">
      <li class="contact-item">
        <svg class="contact-item__icon" viewBox="0 0 30 30" aria-hidden="true">
          <rect width="30" height="30" rx="4"/>
          <path class="glyph" d="M15 6a6 6 0 0 0-6 6c0 4.5 6 11 6 11s6-6.5 6-11a6 6 0 0 0-6-6zm0 8.5a2.5 2.5 0 1 1 0-5 2.5 2.5 0 0 1 0 5z"/>
        </svg>
        <span>7732 FERNGLEN PASS LN AUSTIN, TX 78734</span>
      </li>
      <li class="contact-item">
        <svg class="contact-item__icon" viewBox="0 0 30 30" aria-hidden="true">
          <rect width="30" height="30" rx="4"/>
          <path class="glyph" d="M10.5 7l3 3.5-1.8 2c1 2 2.8 3.8 4.8 4.8l2-1.8 3.5 3-1.8 2.8c-5.8-.4-11.1-5.7-11.5-11.5z"/>
        </svg>
        <span>(512)555-0193</span>
      </li>
      <li class="contact-item">
        <svg class="contact-item__icon" viewBox="0 0 30 30" aria-hidden="true">
          <rect width="30" height="30" rx="4"/>
          <rect class="glyph" x="7" y="9.5" width="16" height="11" rx="1" style="fill:var(--icon-glyph)"/>
          <path class="glyph-line" d="M7.5 10l7.5 6 7.5-6" style="stroke:var(--accent)"/>
        </svg>
        <span>PEARLWOODFRAMINGWORKS@MAILNEST.EXAMPLE</span>
      </li>
    </ul>
  </article>
</main>
</body>
</html>
```